ULMIRA card Technical Architecture

Hello everyone ULMIRA: It is a consulting firm in Architecture and Construction. I require a card duplexing, sober, elegant, classic but not boring. Update 1: Use the following data for the card. Name: Gonzalo Pereda Mauricio Villalta Position: COO Twitter: @ulmiraAT Homepage: ulmira-example.com home address not include the participation of all thank you.

Target Market(s)

Construction companies, Architects and Consulting Engineers

Industry/Entity Type

Consulting

Contact Information for Business Card

Los campos que debe tener:
Nombre, Cargo, email, homepage y twitter

Font styles to use
Serif
Sans Serif
Other font styles liked:
• Me gustan playfair display, open sans y roboto, pero estoy sujeto a sus propuestas

Requirements
Must have
• Colors: Present combined proposals in white, red, gray and black Update 1: The two names must be clearly differentiated from the two surnames
Nice to have
• They are free to present their best proposals. I will bring them immediate feedback to the extent you can go see their designs. Complete data for card and logo files will give the winner the

```html
<!DOCTYPE html>
<html lang="es">
<head>
<meta charset="utf-8">
<title>ULMIRA – Tarjeta de presentación</title>
<link href="https://fonts.googleapis.com/css2?family=Montserrat:wght@400;500;700&display=swap" rel="stylesheet">
<style>
  :root {
    --bg: #3a3a3c;
    --card: #050505;
    --white: #ffffff;
    --grey: #9a9a9a;
    --red: #c4231f;
    --divider: #6b6b6b;
  }
  * { margin: 0; padding: 0; box-sizing: border-box; }
  html, body {
    width: 1200px;
    height: 900px;
    overflow: hidden;
    background: var(--bg);
    font-family: "Montserrat", Arial, sans-serif;
    color: var(--white);
  }
  .canvas {
    position: relative;
    width: 1200px;
    height: 900px;
  }
  .card {
    position: absolute;
    width: 640px;
    height: 366px;
    background: var(--card);
    border-radius: 22px;
    box-shadow: 0 14px 30px rgba(0,0,0,.45);
  }
  .card--front { left: 120px; top: 60px; }
  .card--back  { left: 440px; top: 474px; }

  /* Front */
  .front-brand {
    position: absolute;
    left: 0; right: 0; top: 132px;
    display: flex;
    justify-content: center;
    align-items: center;
    gap: 16px;
  }
  .brand-square {
    width: 26px; height: 26px;
    background: var(--red);
  }
  .front-brand .brand-name {
    font-size: 54px;
    font-weight: 500;
    letter-spacing: 12px;
    color: var(--white);
  }
  .social-handle {
    position: absolute;
    left: 0; right: 0; top: 296px;
    display: flex;
    justify-content: center;
    align-items: center;
    gap: 10px;
    font-size: 15px;
    font-weight: 400;
  }
  .social-dot {
    width: 10px; height: 10px;
    border-radius: 50%;
    background: var(--white);
  }

  /* Back */
  .back-brand {
    position: absolute;
    left: 190px; top: 70px;
    display: flex;
    align-items: center;
    gap: 14px;
  }
  .back-brand .brand-name {
    font-size: 42px;
    font-weight: 500;
    letter-spacing: 14px;
    color: var(--white);
  }
  .brand-square--small { width: 18px; height: 18px; }

  .person {
    position: absolute;
    left: 60px; top: 200px;
    width: 300px;
    text-align: right;
  }
  .person-given, .person-surname {
    font-size: 24px;
    font-weight: 700;
    line-height: 1.1;
  }
  .person-role {
    font-size: 15px;
    font-weight: 400;
    margin-bottom: 12px;
  }
  .person-role--title { font-size: 14px; }

  .divider {
    position: absolute;
    left: 382px; top: 190px;
    width: 1px; height: 120px;
    background: linear-gradient(to bottom, transparent, var(--divider), transparent);
  }
  .contact-list {
    position: absolute;
    left: 404px; top: 200px;
    list-style: none;
    font-size: 14px;
    line-height: 1.75;
  }
  .contact-list li {
    display: flex;
    align-items: center;
    gap: 8px;
  }
  .contact-icon { width: 11px; height: 11px; flex: none; }
</style>
</head>
<body>
<main class="canvas">

  <section class="card card--front" aria-label="Cara frontal">
    <div class="front-brand">
      <span class="brand-square"></span>
      <span class="brand-name">ULMIRA</span>
    </div>
    <p class="social-handle"><span class="social-dot"></span>@ulmiraAT</p>
  </section>

  <section class="card card--back" aria-label="Cara posterior">
    <div class="back-brand">
      <span class="brand-square brand-square--small"></span>
      <span class="brand-name">ULMIRA</span>
    </div>

    <div class="person">
      <p class="person-given">Mauricio Gonzalo</p>
      <p class="person-role">COO</p>
      <p class="person-surname">Pereda Villalta</p>
      <p class="person-role person-role--title">Director de Operaciones</p>
    </div>

    <div class="divider"></div>

    <ul class="contact-list">
      <li>
        <svg class="contact-icon" viewBox="0 0 12 12" aria-hidden="true"><path d="M2.5 1 L4.5 1 L5 3.5 L3.8 4.5 Q5 7 7.5 8.2 L8.5 7 L11 7.5 L11 9.5 Q10.5 11 9 11 Q1 10 1 2.5 Q1 1 2.5 1Z" fill="#fff"/></svg>
        (+571) 555 010 2040
      </li>
      <li>
        <svg class="contact-icon" viewBox="0 0 12 12" aria-hidden="true"><rect x="1" y="2.5" width="10" height="7" fill="none" stroke="#fff" stroke-width="1.3"/><path d="M1 2.5 L6 6.5 L11 2.5" fill="none" stroke="#fff" stroke-width="1.3"/></svg>
        info@ulmira-example.com
      </li>
      <li>
        <svg class="contact-icon" viewBox="0 0 12 12" aria-hidden="true"><circle cx="6" cy="6" r="5" fill="none" stroke="#fff" stroke-width="1.2"/><ellipse cx="6" cy="6" rx="2.2" ry="5" fill="none" stroke="#fff" stroke-width="1"/><path d="M1 6 H11" stroke="#fff" stroke-width="1"/></svg>
        www.ulmira-example.com
      </li>
    </ul>
  </section>

</main>
</body>
</html>
```